Vernac Law Business cards and stationary design project

We are looking for a stationary design for business cards (double sided), 8x10, 5x7, and legal and standard envelopes.

We would like the design to match the logo that we have already.
Color palate preferred is Teal, White, grey and any others that will look good for a professional law firm.

We would like this statement: "RELATIONSHIPS. RESPECT. RESULT" to be on the back of the business cards and maybe on the stationary if it looks good.

Please see link to website for more information: www.vernac-law.example

Target Market(s)

Potential clients that need Attorney services.

Industry/Entity Type

Law Firm

Contact Information for Business Card

We would like the front and back to be two different colors. Current business cards are teal front, grey back and are a vertical design. We are open to options with colors.

Font styles to use
Serif

Colors
33a6d7
33b8a4
b9b9b9
5c5c5c

Requirements
Must have
• Logo supplied needs to go on the card and stationary.
• Match website color palate, www.vernac-law.example
• Be professional and not too wordy.
• Criminal Law, Civil Litigation, Personal Injury, Restraining Orders need to be on the card.
Nice to have
• RELATIONSHIPS. RESPECT. RESULTS. on the back of the card.
Should not have
• Not be too busy/wordy or too flashy.

```html
<!DOCTYPE html>
<html lang="en">
<head>
<meta charset="utf-8">
<title>Vernac Law – Business Card</title>
<link rel="stylesheet" href="https://fonts.googleapis.com/css2?family=Source+Sans+3:wght@400;600&display=swap">
<style>
  :root {
    --backdrop: #3d3d3d;
    --card: #050505;
    --teal: #2a97a6;
    --white: #f2f2f2;
    --grey-band: #6b6b6b;
  }
  * { box-sizing: border-box; margin: 0; padding: 0; }
  html, body {
    width: 1200px; height: 820px; overflow: hidden;
    background: var(--backdrop);
    font-family: "Source Sans 3", "Segoe UI", sans-serif;
  }
  .card {
    position: absolute; top: 257px;
    width: 477px; height: 275px;
    background: var(--card);
    overflow: hidden;
  }
  .card--front { left: 115px; }
  .card--back  { left: 621px; }

  .practice-areas {
    position: absolute; top: 26px; left: 0; width: 100%;
    display: flex; align-items: center; justify-content: center; gap: 8px;
    color: var(--white); font-size: 14px;
  }
  .practice-areas::before, .practice-areas::after {
    content: ""; width: 42px; height: 2px; background: var(--teal);
  }

  .front-name {
    position: absolute; left: 30px; top: 118px; width: 200px;
    text-align: center;
    color: var(--teal); font-weight: 600; font-size: 30px; line-height: 1.1;
  }
  .divider {
    position: absolute; left: 240px; top: 64px;
    width: 1px; height: 142px;
    background: linear-gradient(to bottom, transparent, #8a8a8a 20%, #8a8a8a 80%, transparent);
  }

  .contact { position: absolute; left: 265px; top: 63px; color: var(--white); }
  .contact__name { color: var(--teal); font-weight: 600; font-size: 17px; line-height: 1.2; }
  .contact__title { font-size: 13px; margin-top: 1px; }
  .contact__list { list-style: none; margin-top: 14px; font-size: 12.5px; line-height: 16px; }
  .contact__item { display: flex; gap: 5px; align-items: flex-start; margin-bottom: 2px; }
  .contact__item--address { margin-bottom: 7px; }
  .contact__item svg { width: 11px; height: 11px; margin-top: 3px; flex: none; fill: var(--teal); }

  .footer-band {
    position: absolute; left: 0; bottom: 0; width: 100%; height: 26px;
    background: var(--grey-band);
    border-top: 2px solid var(--teal);
    display: flex; align-items: center; justify-content: center;
  }
  .motto { color: var(--white); font-size: 13px; }

  .back-name {
    position: absolute; left: 0; top: 160px; width: 100%;
    text-align: center;
    color: var(--teal); font-size: 34px; font-weight: 400; letter-spacing: 2px;
    text-transform: uppercase;
  }
</style>
</head>
<body>

<section class="card card--front">
  <p class="practice-areas">Criminal Law Civil Litigation Personal Injury</p>

  <p class="front-name">Vernac<br>Law</p>
  <div class="divider"></div>

  <div class="contact">
    <p class="contact__name">Mara Ellison</p>
    <p class="contact__title">Attorney at Law</p>
    <ul class="contact__list">
      <li class="contact__item contact__item--address">
        <svg viewBox="0 0 12 12" aria-hidden="true"><path d="M6 0a4 4 0 0 0-4 4c0 3 4 8 4 8s4-5 4-8a4 4 0 0 0-4-4zm0 5.6A1.6 1.6 0 1 1 6 2.4a1.6 1.6 0 0 1 0 3.2z"/></svg>
        <span>Central Oregon,<br>4100 Calloway Ave. #12</span>
      </li>
      <li class="contact__item">
        <svg viewBox="0 0 12 12" aria-hidden="true"><path d="M2.4 0.6l1.8 2.2-1 1.3c.8 1.7 2 2.9 3.7 3.7l1.3-1 2.2 1.8-.8 2.2C5.4 10.6 1.4 6.6 0.2 1.4z"/></svg>
        <span>(555) 014-2290</span>
      </li>
      <li class="contact__item">
        <svg viewBox="0 0 12 12" aria-hidden="true"><path d="M0 2h12v1.2L6 7 0 3.2z M0 4.6l6 3.8 6-3.8V10H0z"/></svg>
        <span>mara@vernac-law.example</span>
      </li>
      <li class="contact__item">
        <svg viewBox="0 0 12 12" aria-hidden="true"><circle cx="6" cy="6" r="5.5"/><path d="M0.5 6h11M6 0.5c-2 2.5-2 8.5 0 11M6 0.5c2 2.5 2 8.5 0 11" stroke="#050505" stroke-width="0.8" fill="none"/></svg>
        <span>www.vernac-law.example</span>
      </li>
    </ul>
  </div>

  <div class="footer-band">
    <p class="motto">Relationships Respect Results</p>
  </div>
</section>

<section class="card card--back">
  <p class="back-name">Vernac Law</p>
</section>

</body>
</html>
```